Business card design for a dynamic IT consulting company

We need a business card design for a young firm, specialized in the Telecommunications/Consulting industry. The name of the company is Quindor and Partners Business Consulting Ltd. (Short name: Quindor and Partnes)
Quindor = solve read reverse, so we aim to be uncomplicated and solution-oriented. The small pipe in our logo is also related to the word solve. So we need a new business card design, which is simple, eye catching and something non traditional (I would probably prefer a square shaped design rather than a rectangle, but open for suggestions). Attached our logo.

Target Market(s)

Usually our customers are Tier1 Telecoms providers (Q-Netra, Palorix, etc) and their executives.

Industry/Entity Type

Business

Contact Information for Business Card

Name: Bence Tolnavari
Email: b.tolnavari@quindor.hu
Web: www.quindor.hu
Mobile: +36 30 518 2769
Title: Managing Director

Optional:
Company name: Quindor and Partners Ltd.
Address: 1087 Budapest, Tolvenka str. 28/C, Hungary

Font styles to use
Other font styles liked:
• helveticaneue_medium, Prime Regular are used now.

Colors

Designer to choose colors to be used in the design.

Requirements
Must have
• I would like to have a 2 sided design.
Nice to have
• I thought if we make the logo a bit bigger (without the company name), that could go to the back with the company name below. I though, if the pipe in the logo is somehow touchable on the business card, would be nice and unique.

```html
<!DOCTYPE html>
<html lang="en">
<head>
<meta charset="utf-8">
<title>Quindor and Partners – Business Card</title>
<link rel="stylesheet" href="https://fonts.googleapis.com/css2?family=Exo+2:wght@500;600&family=Work+Sans:wght@400;500&display=swap">
<style>
  :root {
    --backdrop: #d9d4ce;
    --card: #efedea;
    --ink-grey: #555453;
    --ink-soft: #6e6c6a;
    --magenta: #a8205f;
    --teal: #2a9bb0;
    --teal-text: #1f8fa3;
    --on-magenta: #f6e8ef;
  }
  html, body {
    margin: 0;
    width: 1200px;
    height: 1047px;
    overflow: hidden;
    background: var(--backdrop);
  }
  .card {
    position: absolute;
    left: 80px;
    top: 241px;
    width: 875px;
    height: 475px;
    transform: scale(1.19);
    transform-origin: top left;
    background: var(--card);
    border-radius: 18px;
    overflow: hidden;
    font-family: "Work Sans", Arial, sans-serif;
  }
  .card-band {
    position: absolute;
    inset: 0;
    width: 875px;
    height: 475px;
  }
  .brand {
    position: absolute;
    left: 60px;
    top: 52px;
    display: flex;
    align-items: center;
    gap: 18px;
  }
  .brand-square {
    width: 36px;
    height: 36px;
    background: var(--magenta);
  }
  .brand-name {
    font-size: 44px;
    font-weight: 500;
    color: var(--ink-grey);
    line-height: 1;
  }
  .person {
    position: absolute;
    left: 55px;
    top: 212px;
  }
  .person-name {
    font-family: "Exo 2", Arial, sans-serif;
    font-weight: 500;
    font-size: 27px;
    letter-spacing: 1.5px;
    color: var(--teal-text);
    line-height: 1;
  }
  .person-title {
    margin-top: 10px;
    font-size: 18px;
    color: var(--ink-soft);
  }
  .contact {
    position: absolute;
    right: 55px;
    top: 265px;
    color: var(--on-magenta);
    font-size: 17px;
    letter-spacing: 0.4px;
  }
  .contact-line {
    display: flex;
    justify-content: flex-end;
    align-items: center;
    gap: 14px;
    height: 26px;
  }
  .contact-icon { width: 15px; height: 15px; }
  .company {
    position: absolute;
    right: 84px;
    top: 362px;
    text-align: right;
    color: var(--on-magenta);
    font-size: 17px;
    line-height: 25px;
    letter-spacing: 0.4px;
  }
  .company-name {
    font-family: "Exo 2", Arial, sans-serif;
    font-weight: 600;
    font-size: 19px;
    letter-spacing: 1px;
    color: var(--teal);
  }
</style>
</head>
<body>
  <div class="card">
    <svg class="card-band" viewBox="0 0 875 475" aria-hidden="true">
      <path d="M0,420 C300,420 560,240 875,200 L875,475 L0,475 Z" fill="var(--magenta)"/>
      <path d="M0,395 C300,395 560,215 875,175" fill="none" stroke="var(--teal)" stroke-width="4"/>
    </svg>

    <div class="brand">
      <div class="brand-square"></div>
      <div class="brand-name">Quindor and Partners</div>
    </div>

    <div class="person">
      <div class="person-name">BENCE TOLNAVARI</div>
      <div class="person-title">Managing Director</div>
    </div>

    <div class="contact">
      <div class="contact-line">+36 30 518 2769
        <svg class="contact-icon" viewBox="0 0 16 16" aria-hidden="true"><path d="M4 1l3 3-2 2c1 2 3 4 5 5l2-2 3 3-2 3C7 15 1 9 1 3z" fill="var(--on-magenta)"/></svg>
      </div>
      <div class="contact-line">b.tolnavari@quindor.hu
        <svg class="contact-icon" viewBox="0 0 16 16" aria-hidden="true"><rect x="1" y="3" width="14" height="10" fill="var(--on-magenta)"/><path d="M1 3l7 6 7-6" fill="none" stroke="var(--magenta)" stroke-width="1.4"/></svg>
      </div>
      <div class="contact-line">www.quindor.hu
        <svg class="contact-icon" viewBox="0 0 16 16" aria-hidden="true"><g fill="none" stroke="var(--on-magenta)" stroke-width="1.4"><circle cx="8" cy="8" r="6.5"/><ellipse cx="8" cy="8" rx="3" ry="6.5"/><path d="M1.5 8h13"/></g></svg>
      </div>
    </div>

    <div class="company">
      <div class="company-name">QUINDOR AND PARTNERS LTD.</div>
      <div>1087 Budapest, Tolvenka</div>
      <div>str. 28/C, Hungary</div>
    </div>
  </div>
</body>
</html>
```